Harbourline Electrical Solutions

On one side. LOGO (underneath:) Commercial Industrial Residential

- NAME & CONTACT DETAILS

Marcus T. Hollings
Project Manager

(Cell icon) (441) 555-0187
(Email icon) hlelectricalsolutions@mailvento.com
(Facebook & Instagram icons )@hlelectricalsolutions

Other side: LOGO - underneath ELECTRICAL CONSTRUCTION & MAINTENANCE . LED LIGHTING & AUTOMATION . LIFE SAFETY SYSTEMS (FIRE ALARM / SECURITY) . DATA & COMMUNICATION

```html
<!DOCTYPE html>
<html lang="en">
<head>
<meta charset="utf-8">
<title>Harbourline Electrical Solutions – Business Card</title>
<link rel="stylesheet" href="https://fonts.googleapis.com/css2?family=Montserrat:wght@400;500;600&family=Exo+2:ital,wght@1,600&display=swap">
<style>
  :root {
    --backdrop: #3a3a3c;
    --card: #222224;
    --card-edge: #19191a;
    --ink-light: #f2f2f2;
    --ink-grey: #9a9a9d;
    --ink-mark: #2c2c2e;
    --accent-blue: #1a8fd8;
    --teal: #0d5a78;
    --teal-bright: #1f7fa3;
    --wave-grey: #4a4f53;
  }
  * { margin: 0; padding: 0; box-sizing: border-box; }
  html, body { width: 799px; height: 1200px; overflow: hidden; }
  body {
    background: var(--backdrop);
    font-family: "Montserrat", Arial, sans-serif;
    position: relative;
  }
  .card {
    position: absolute;
    left: 80px;
    width: 640px;
    height: 366px;
    background: var(--card);
    border-radius: 4px;
    overflow: hidden;
    box-shadow: 0 10px 28px rgba(0,0,0,.45);
  }
  .card--front { top: 170px; }
  .card--back { top: 660px; }

  /* front */
  .front-brand {
    position: absolute; left: 150px; top: 48px;
    display: flex; align-items: center; gap: 22px;
  }
  .brand-square {
    width: 64px; height: 64px;
    background: var(--ink-mark);
    border: 1px solid #333;
  }
  .brand-divider { width: 1px; height: 90px; background: #555; }
  .front-brand .brand-name {
    font-size: 24px; font-weight: 500; line-height: 1.18;
    letter-spacing: 5px; text-transform: uppercase;
    color: var(--ink-grey);
  }
  .services {
    position: absolute; left: 44px; top: 178px;
    font-size: 13.5px; color: var(--ink-light); line-height: 1.55;
  }
  .services .sep { margin: 0 6px; }
  .front-rule {
    position: absolute; left: 30px; right: 30px; top: 236px;
    height: 1.5px; background: var(--accent-blue);
  }
  .sectors {
    font-size: 14px; font-weight: 500; letter-spacing: 3px;
    text-transform: uppercase; color: var(--ink-light);
  }
  .card--front .sectors { position: absolute; left: 44px; top: 268px; }
  .sectors .sep { margin: 0 14px; }

  /* back */
  .back-brand {
    position: absolute; left: 42px; top: 36px;
  }
  .back-brand .brand-name {
    font-size: 25px; font-weight: 600; letter-spacing: 4px;
    text-transform: uppercase; color: var(--teal-bright);
    line-height: 1.15;
  }
  .card--back .sectors {
    margin-top: 10px; font-size: 12px; letter-spacing: 2.5px; color: var(--ink-grey);
  }
  .card--back .sectors .sep { margin: 0 10px; }
  .contact-list {
    position: absolute; left: 42px; top: 150px;
    list-style: none; font-size: 13px; color: var(--ink-light);
  }
  .contact-list li { display: flex; align-items: center; gap: 10px; margin-bottom: 8px; }
  .contact-list svg { width: 14px; height: 14px; fill: var(--teal-bright); }
  .social-dot { width: 11px; height: 11px; border-radius: 50%; background: var(--teal-bright); margin-left: 1.5px; }
  .wave { position: absolute; left: 0; bottom: 0; width: 640px; height: 200px; }
  .person {
    position: absolute; right: 40px; bottom: 34px; text-align: right;
    color: #fff;
  }
  .person-name {
    font-family: "Exo 2", Arial, sans-serif; font-style: italic; font-weight: 600;
    font-size: 27px; letter-spacing: .3px;
  }
  .person-role { font-size: 15px; margin-top: 2px; }
</style>
</head>
<body>

<section class="card card--front" aria-label="Card front">
  <div class="front-brand">
    <div class="brand-square"></div>
    <div class="brand-divider"></div>
    <div class="brand-name">Harbourline<br>Electrical<br>Solutions</div>
  </div>
  <div class="services">
    <p>Electrical Construction &amp; Maintenance<span class="sep">|</span>Led Lighting &amp; Automation</p>
    <p>Life Safety Systems (Fire Alarm/Security)<span class="sep">|</span>Data &amp; Communication</p>
  </div>
  <div class="front-rule"></div>
  <p class="sectors">Commercial<span class="sep">|</span>Industrial<span class="sep">|</span>Residential</p>
</section>

<section class="card card--back" aria-label="Card back">
  <div class="back-brand">
    <div class="brand-name">Harbourline Electrical Solutions</div>
    <p class="sectors">Commercial<span class="sep">|</span>Industrial<span class="sep">|</span>Residential</p>
  </div>

  <ul class="contact-list">
    <li>
      <svg viewBox="0 0 24 24" aria-hidden="true"><path d="M6.6 10.8a15.1 15.1 0 0 0 6.6 6.6l2.2-2.2c.3-.3.7-.4 1-.2 1.1.4 2.3.6 3.6.6.6 0 1 .4 1 1V20c0 .6-.4 1-1 1C10.6 21 3 13.4 3 4c0-.6.4-1 1-1h3.5c.6 0 1 .4 1 1 0 1.3.2 2.5.6 3.6.1.3 0 .7-.2 1z"/></svg>
      <span>(441) 555-0187</span>
    </li>
    <li>
      <svg viewBox="0 0 24 24" aria-hidden="true"><path d="M2 5h20v14H2zm2 2v.5l8 5 8-5V7l-8 5z"/></svg>
      <span>hlelectricalsolutions@mailvento.com</span>
    </li>
    <li>
      <span class="social-dot"></span>
      <span>@hlelectricalsolutions</span>
    </li>
  </ul>

  <svg class="wave" viewBox="0 0 640 200" preserveAspectRatio="none" aria-hidden="true">
    <path d="M0 40 C90 110 250 140 390 120 C500 105 590 110 640 140 L640 200 L0 200 Z" fill="var(--wave-grey)"/>
    <path d="M0 60 C110 125 260 150 400 135 C510 125 595 130 640 155 L640 200 L0 200 Z" fill="var(--card)"/>
    <path d="M0 70 C120 140 270 165 410 150 C515 140 600 145 640 165 L640 200 L0 200 Z" fill="var(--teal)"/>
    <path d="M0 95 C140 175 300 170 430 160 C530 153 605 158 640 175" fill="none" stroke="var(--wave-grey)" stroke-width="2" opacity=".5"/>
  </svg>

  <div class="person">
    <p class="person-name">Marcus T. Hollings</p>
    <p class="person-role">Project Manager</p>
  </div>
</section>

</body>
</html>
```